Company or website name
- Quiet Hollow Properties
- Describe your company and organization and target audience
- We sell rural vacant, mostly residential land. Our target market is looking for privacy and either a place to retire to or a place to escape to.
- The design should have the following
- Mountains, Pine Trees, Earthy Colors, and match the attached logo. The home page should have designs for slides of properties at the top, followed by a survey (for users to share details of the property they're looking for), followed by search functionality, individual properties and general areas properties are available in. We'll also need at least one contact form on each page as well as maps. For the property detail page we'll need a large area for pictures, highlighted property details, a description and more detailed facts about property. The property detail page should also have a survey for users to share details of what they're looking for and contact form. Last but not least, similar properties should also be included on the property listing page. The winning design will include an excellent "Contact Us" page! Every page should have an opt-in offering users to be notified when new properties become available.
- Briefly describe your contest

```html
<!DOCTYPE html>
<html lang="en">
<head>
<meta charset="utf-8">
<title>Quiet Hollow Properties</title>
<link href="https://fonts.googleapis.com/css2?family=Montserrat:wght@300;400;500;600;700&display=swap" rel="stylesheet">
<style>
:root{
  --blue:#1e8fe6;
  --blue-dark:#0b5fae;
  --green:#6f9b2c;
  --green-dark:#5a8420;
  --ink:#333;
  --muted:#888;
  --light:#f4f6f8;
  --ghost:#eeeeee;
  --footer:#232323;
  --white:#fff;
}
*{box-sizing:border-box;margin:0;padding:0}
html,body{width:1200px;height:4909px;overflow:hidden}
body{font-family:'Montserrat',sans-serif;color:var(--ink);background:var(--white);position:relative}
section,header,footer,.topbar{position:absolute;left:0;width:1200px}
.abs{position:absolute}

/* top bar */
.topbar{top:0;height:34px;font-size:9px;color:#555;display:flex;align-items:center;padding:0 63px;gap:20px}
.topbar .lang{margin-left:auto}
.topbar svg{vertical-align:-1px;margin-right:4px}

/* header */
.site-header{top:34px;height:73px;display:flex;align-items:center;padding:0 63px}
.brand{display:flex;align-items:center;gap:8px;font-weight:700;font-size:13px;color:#2c4a1c}
.brand .dot{width:34px;height:34px;border-radius:50%;background:#2c4a1c}
.nav{margin-left:auto;display:flex;gap:34px;font-size:10px;align-items:center}
.nav a{color:#333;text-decoration:none}
.nav a.active{color:var(--blue)}
.nav .signup{border:2px solid #3a5070;padding:8px 18px;border-radius:3px;margin-left:8px}

/* hero */
.hero{top:107px;height:457px;background:linear-gradient(180deg,#4b5a46 0%,#2d3a2a 45%,#3f3e2e 75%,#2a2a22 100%)}
.hero h1{position:absolute;top:128px;width:100%;text-align:center;color:#fff;font-weight:400;font-size:27px;letter-spacing:1px}
.searchbar{position:absolute;left:234px;top:198px;width:732px;height:72px;background:var(--blue);display:flex;align-items:center;padding:0 14px;gap:10px}
.searchbar .search-label{flex:none;color:#fff;font-weight:700;font-size:11px;line-height:12px;display:flex;align-items:center;gap:8px;width:92px}
.searchbar .search-field{flex:none;height:26px;border:1px solid rgba(255,255,255,.4);background:rgba(255,255,255,.12);color:#fff;font-size:8px;display:flex;align-items:center;padding:0 10px;justify-content:space-between}
.searchbar .search-btn{flex:none;height:26px;background:var(--blue-dark);color:#fff;font-size:8px;font-weight:700;display:flex;align-items:center;justify-content:center;width:92px}
.hero .arrow{position:absolute;top:210px}

/* looking for */
.looking{top:564px;height:606px;background:linear-gradient(180deg,#6e9a2d,#79a434 50%,#6a9529);color:#fff}
.looking h2{position:absolute;top:70px;width:100%;text-align:center;font-weight:400;font-size:19px}
.cat{position:absolute;top:142px;width:244px;text-align:center}
.cat .ring{width:146px;height:146px;border-radius:50%;border:4px solid #fff;margin:0 auto;display:flex;align-items:center;justify-content:center}
.cat h3{font-size:18px;font-weight:700;margin-top:14px}
.cat p{font-size:11px;line-height:18px;margin-top:6px}
.outline-btn{display:inline-block;border:2px solid #fff;padding:7px 28px;font-size:8px;margin-top:12px}
.or{position:absolute;top:440px;left:234px;width:732px;text-align:center;font-size:12px}
.or::before,.or::after{content:"";position:absolute;top:8px;width:330px;border-top:1px solid rgba(255,255,255,.4)}
.or::before{left:0}.or::after{right:0}
.findrow{position:absolute;top:488px;left:388px;width:452px;height:42px;display:flex}
.findrow .sel{flex:1;border:2px solid #fff;display:flex;align-items:center;justify-content:space-between;padding:0 16px;font-size:9px}
.findrow .go{width:86px;background:#fff;color:#333;font-size:10px;display:flex;align-items:center;justify-content:center}

/* section heading with ghost */
.heading{position:absolute;width:100%;text-align:center}
.heading .ghost{font-size:38px;color:var(--ghost);font-weight:400;letter-spacing:1px}
.heading .title{position:absolute;left:0;right:0;top:20px;font-size:20px;font-weight:400;color:#333}

/* latest */
.latest{top:1170px;height:906px}
.tabs{position:absolute;top:140px;left:506px;display:flex}
.tabs span{width:94px;height:30px;display:flex;align-items:center;justify-content:center;font-size:10px;border:1px solid #ddd}
.tabs .on{background:var(--blue);color:#fff;border-color:var(--blue)}
.prop{position:absolute;width:231px}
.prop .photo{height:198px;position:relative}
.prop .fav{position:absolute;right:12px;bottom:-10px;width:28px;height:28px;border-radius:50%;background:var(--green);display:flex;align-items:center;justify-content:center}
.prop .loc{font-size:7px;color:#999;margin-top:16px}
.prop .name{font-size:13px;margin-top:4px}
.prop .price{font-size:10px;color:#888;margin-top:6px}
.prop .price b{color:var(--green)}
.view-all{position:absolute;left:550px;width:100px;height:30px;border:2px solid #333;font-size:8px;display:flex;align-items:center;justify-content:center}

/* areas */
.areas{top:2076px;height:477px}
.area{position:absolute;top:141px;width:200px;height:261px;color:#fff;text-align:center}
.area .nm{position:absolute;bottom:36px;width:100%;font-size:13px}
.area .ct{position:absolute;bottom:20px;width:100%;font-size:8px}
.circ-arrow{position:absolute;width:38px;height:38px;border-radius:50%;background:#fff;box-shadow:0 1px 6px rgba(0,0,0,.25);display:flex;align-items:center;justify-content:center}

/* why */
.why{top:2595px;height:225px;background:linear-gradient(180deg,#39413a,#262d26);color:#fff;text-align:center}
.why small{display:block;margin-top:68px;font-size:9px}
.why h2{font-weight:400;font-size:19px;margin-top:10px}
.why .cta{display:inline-block;background:var(--green);padding:9px 22px;font-size:8px;margin-top:16px}

/* testimonials */
.testi{top:2820px;height:485px}
.person{position:absolute;top:180px;width:250px;text-align:center}
.person .av{width:76px;height:76px;border-radius:50%;margin:0 auto;background:radial-gradient(circle,#c9c9c9,#8b8b8b)}
.person h4{font-size:11px;font-weight:600;margin-top:18px}
.person .role{font-size:7px;color:#aaa;margin-top:3px}
.person p{font-size:9.5px;line-height:16px;color:#666;margin-top:12px}
.pager{position:absolute;top:430px;width:100%;text-align:center;font-size:9px;color:#666}

/* blog */
.blog{top:3305px;height:486px}
.post{position:absolute;top:131px;width:200px}
.post .photo{height:157px}
.post .meta{font-size:7px;color:#aaa;margin-top:8px}
.post .meta b{font-weight:400;color:#555}
.post h4{font-size:12.5px;font-weight:400;line-height:18px;margin-top:6px}
.post p{font-size:8.5px;line-height:14px;color:#777;margin-top:6px}
.post .more{font-size:9px;color:#555;margin-top:12px}

/* partners */
.partners{top:3791px;height:248px}
.partner-row{position:absolute;top:130px;left:260px;width:680px;display:flex;justify-content:space-between;align-items:center;font-size:11px;color:#444;letter-spacing:1px}
.partner-row span{display:flex;align-items:center;gap:6px}
.partner-row i{width:10px;height:10px;border-radius:50%;background:#555;display:inline-block}

/* notify */
.notify{top:4039px;height:139px;background:var(--green);color:#fff}
.notify h3{position:absolute;left:232px;top:36px;font-size:17px;font-weight:400;line-height:23px}
.notify .input{position:absolute;left:522px;top:50px;width:330px;height:34px;background:rgba(0,0,0,.12);font-size:8px;display:flex;align-items:center;padding-left:14px}
.notify .btn{position:absolute;left:860px;top:50px;width:100px;height:34px;background:rgba(0,0,0,.22);font-size:10px;font-weight:600;display:flex;align-items:center;justify-content:center}

/* contact */
.contact{top:4178px;height:428px;background:var(--light)}
.form-field{position:absolute;height:30px;border:1px solid #dcdfe3;background:#fff;font-size:8px;padding:10px 12px}
.send{position:absolute;left:234px;top:334px;width:465px;height:38px;background:var(--blue);color:#fff;font-size:11px;font-weight:700;display:flex;align-items:center;justify-content:center}

/* footer */
.site-footer{top:4606px;height:303px;background:var(--footer);color:#ddd}
.fcol{position:absolute;top:60px;font-size:8.5px}
.fcol h5{font-size:9.5px;font-weight:500;color:#fff;margin-bottom:18px}
.fcol li{list-style:none;margin-bottom:14px}
.fcol li svg{vertical-align:-2px;margin-right:6px}
.copy{position:absolute;bottom:12px;width:100%;text-align:center;font-size:8px;color:#777}
.copy b{color:var(--blue);font-weight:400}
</style>
</head>
<body>

<div class="topbar">
  <span><svg width="9" height="9" viewBox="0 0 24 24"><path fill="#555" d="M6.6 10.8a15 15 0 006.6 6.6l2.2-2.2c.3-.3.7-.4 1-.2 1.1.4 2.3.6 3.6.6.6 0 1 .4 1 1V20c0 .6-.4 1-1 1A17 17 0 013 4c0-.6.4-1 1-1h3.5c.6 0 1 .4 1 1 0 1.3.2 2.5.6 3.6.1.3 0 .7-.2 1z"/></svg>+020 5550 1234</span>
  <span><svg width="9" height="9" viewBox="0 0 24 24"><path fill="#555" d="M2 5h20v14H2z"/></svg>hello@quiethollowproperties.com</span>
  <span class="lang">EN ▾</span>
</div>

<header class="site-header">
  <div class="brand"><span class="dot"></span>QUIET HOLLOW PROPERTIES</div>
  <nav class="nav">
    <a class="active">HOME</a><a>ABOUT US</a><a>OUR PROPERTIES</a><a>REVIEWS</a><a>BLOG</a><a>CONTACT US</a><a class="signup">SIGN UP</a>
  </nav>
</header>

<section class="hero" role="img" aria-label="Slide photo of a pine forest and lakeside cabins under mountains">
  <svg class="arrow" style="left:62px" width="16" height="30" viewBox="0 0 16 30"><path d="M14 2L2 15l12 13" stroke="#fff" stroke-width="2" fill="none"/></svg>
  <svg class="arrow" style="right:62px" width="16" height="30" viewBox="0 0 16 30"><path d="M2 2l12 13L2 28" stroke="#fff" stroke-width="2" fill="none"/></svg>
  <h1>FIND YOUR PROPERTY</h1>
  <div class="searchbar">
    <div class="search-label">QUICK<br>SEARCH <svg width="20" height="20" viewBox="0 0 24 24"><circle cx="10" cy="10" r="7" stroke="#fff" stroke-width="3" fill="none"/><path d="M15 15l6 6" stroke="#fff" stroke-width="3"/></svg></div>
    <div class="search-field" style="width:300px">Enter Your Keyword ...</div>
    <div class="search-field" style="width:90px">All City <span>▾</span></div>
    <div class="search-field" style="width:90px">All Type <span>▾</span></div>
    <div class="search-btn">SEARCH ⌕</div>
  </div>
</section>

<section class="looking">
  <h2>WHAT ARE YOU LOOKING FOR?</h2>
  <div class="cat" style="left:234px">
    <div class="ring"><svg width="64" height="64" viewBox="0 0 64 64" fill="none" stroke="#fff" stroke-width="2"><rect x="10" y="12" width="22" height="44"/><rect x="32" y="26" width="22" height="30"/><path d="M16 20h4M24 20h4M16 30h4M24 30h4M16 40h4M24 40h4M38 34h4M46 34h4M38 44h4M46 44h4M18 56v-8h6v8"/></svg></div>
    <h3>APARTMENTS</h3><p>Lorem Ipsum is simply dummy<br>text of the printing</p><span class="outline-btn">VIEW ALL</span>
  </div>
  <div class="cat" style="left:478px">
    <div class="ring"><svg width="64" height="64" viewBox="0 0 64 64" fill="none" stroke="#fff" stroke-width="2"><path d="M6 32L32 10l26 22M14 26v30h36V26"/><rect x="24" y="32" width="16" height="14"/><path d="M32 32v14M24 39h16"/></svg></div>
    <h3>HOUSES</h3><p>Lorem Ipsum is simply dummy<br>text of the printing</p><span class="outline-btn">VIEW ALL</span>
  </div>
  <div class="cat" style="left:722px">
    <div class="ring"><svg width="64" height="64" viewBox="0 0 64 64" fill="none" stroke="#fff" stroke-width="2"><rect x="8" y="12" width="26" height="44"/><rect x="34" y="28" width="22" height="28"/><path d="M14 20h6M24 20h4M14 30h6M24 30h4M14 40h6M24 40h4M40 36h4M48 36h3M40 46h4M48 46h3"/></svg></div>
    <h3>OFFICES</h3><p>Lorem Ipsum is simply dummy<br>text of the printing</p><span class="outline-btn">VIEW ALL</span>
  </div>
  <div class="or">Or</div>
  <div class="findrow"><div class="sel">What are you looking for? <span>⌄</span></div><div class="go">FIND</div></div>
</section>

<section class="latest">
  <div class="heading" style="top:66px"><div class="ghost">OUR PROPERTIES</div><div class="title">LATEST PROPERTIES</div></div>
  <div class="tabs"><span class="on">Sell</span><span>Buy</span></div>

  <div class="prop" style="left:234px;top:215px"><div class="photo" role="img" aria-label="Bright living room interior" style="background:linear-gradient(160deg,#d9d6cf,#a9a49a)"><span class="fav"><svg width="12" height="12" viewBox="0 0 24 24"><path d="M12 21l-8-8a5 5 0 017-7l1 1 1-1a5 5 0 017 7z" stroke="#fff" stroke-width="2" fill="none"/></svg></span></div><div class="loc">Poughkeepsie, New York</div><div class="name">Sky Pool Villa House</div><div class="price">From <b>$20,500</b></div></div>
  <div class="prop" style="left:484px;top:215px"><div class="photo" role="img" aria-label="Living room with property details overlay" style="background:linear-gradient(160deg,#6a6a66,#3c3c3a)"><span class="fav" style="background:var(--blue)"><svg width="12" height="12" viewBox="0 0 24 24"><path d="M12 21l-8-8a5 5 0 017-7l1 1 1-1a5 5 0 017 7z" stroke="#fff" stroke-width="2" fill="none"/></svg></span>
    <div class="abs" style="left:14px;top:104px;color:#fff;font-size:7px;line-height:16px">▪ 2 Bathrooms<br>▪ 2416 sqft<br>▪ 2 Bedrooms<br><br>⌖ 1813 S. 4th Boulevard, Fountain</div></div><div class="loc">Poughkeepsie, New York</div><div class="name">Sky Pool Villa House</div><div class="price">From <b>$20,500</b></div></div>
  <div class="prop" style="left:734px;top:215px"><div class="photo" role="img" aria-label="Log house in snowy pine forest" style="background:linear-gradient(180deg,#cfd5d8,#8a6a45 70%,#5b4630)"><span class="fav"><svg width="12" height="12" viewBox="0 0 24 24"><path d="M12 21l-8-8a5 5 0 017-7l1 1 1-1a5 5 0 017 7z" stroke="#fff" stroke-width="2" fill="none"/></svg></span></div><div class="loc">Poughkeepsie, New York</div><div class="name">Sky Pool Villa House</div><div class="price">From <b>$20,500</b></div></div>

  <div class="prop" style="left:234px;top:525px"><div class="photo" role="img" aria-label="Wooden cabin beneath mountains" style="background:linear-gradient(180deg,#9fb2c3,#5b6b4c 55%,#3f4a32)"><span class="fav"><svg width="12" height="12" viewBox="0 0 24 24"><path d="M12 21l-8-8a5 5 0 017-7l1 1 1-1a5 5 0 017 7z" stroke="#fff" stroke-width="2" fill="none"/></svg></span></div><div class="loc">Poughkeepsie, New York</div><div class="name">Sky Pool Villa House</div><div class="price">From <b>$20,500</b></div></div>
  <div class="prop" style="left:484px;top:525px"><div class="photo" role="img" aria-label="Warm lit living room with fireplace" style="background:linear-gradient(160deg,#e8d8b0,#b08a55)"><span class="fav"><svg width="12" height="12" viewBox="0 0 24 24"><path d="M12 21l-8-8a5 5 0 017-7l1 1 1-1a5 5 0 017 7z" stroke="#fff" stroke-width="2" fill="none"/></svg></span></div><div class="loc">Poughkeepsie, New York</div><div class="name">Sky Pool Villa House</div><div class="price">From <b>$20,500</b></div></div>
  <div class="prop" style="left:734px;top:525px"><div class="photo" role="img" aria-label="White interior with armchair by a window" style="background:linear-gradient(160deg,#eeeeec,#c4c2bd)"><span class="fav"><svg width="12" height="12" viewBox="0 0 24 24"><path d="M12 21l-8-8a5 5 0 017-7l1 1 1-1a5 5 0 017 7z" stroke="#fff" stroke-width="2" fill="none"/></svg></span></div><div class="loc">Poughkeepsie, New York</div><div class="name">Sky Pool Villa House</div><div class="price">From <b>$20,500</b></div></div>

  <div class="view-all" style="top:823px">VIEW ALL</div>
</section>

<section class="areas">
  <div class="abs" style="left:63px;top:60px;font-size:38px;color:var(--ghost)">TOP AREAS</div>
  <div class="abs" style="left:63px;top:80px;font-size:20px">FIND YOUR NEIGHBORHOOD</div>
  <div class="abs" style="right:63px;top:76px;border:2px solid #3a5070;padding:8px 10px;font-size:8px">EXPLORE MORE</div>
  <div class="area" style="left:67px" role="img" aria-label="Snowy cabin among pines at night"><div style="position:absolute;inset:0;background:linear-gradient(180deg,#2b3440,#6b5232 70%,#2a2418)"></div><div class="nm">NEW YORK</div><div class="ct">03 Properties</div></div>
  <div class="area" style="left:286px" role="img" aria-label="Mountain hotel in snow"><div style="position:absolute;inset:0;background:linear-gradient(180deg,#aebfd0,#8d8a84 60%,#55503f)"></div><div class="nm">ALBANY</div><div class="ct">0 Properties</div></div>
  <div class="area" style="left:505px" role="img" aria-label="Villa with pool and hills"><div style="position:absolute;inset:0;background:linear-gradient(180deg,#7c9a6e,#4e6648 55%,#3a7c8a)"></div><div class="nm">ITALY</div><div class="ct">2 Properties</div></div>
  <div class="area" style="left:724px" role="img" aria-label="Green rolling farmland"><div style="position:absolute;inset:0;background:linear-gradient(180deg,#8fa36a,#6a8a3c 60%,#3f4e2c)"></div><div class="nm">DOWNEY</div><div class="ct">5 Properties</div></div>
  <div class="area" style="left:943px" role="img" aria-label="House on a green hillside"><div style="position:absolute;inset:0;background:linear-gradient(180deg,#a8b9a0,#5e7d45 55%,#34442a)"></div><div class="nm">BERLIN</div><div class="ct">1 Properties</div></div>
  <div class="circ-arrow" style="left:48px;top:252px">←</div>
  <div class="circ-arrow" style="left:1120px;top:252px">→</div>
</section>

<section class="why" role="img" aria-label="Dark background photo of wooden cabins">
  <small>Why Choose Our Properties</small>
  <h2>The experts in local and international property</h2>
  <span class="cta">GET STARTED</span>
</section>

<section class="testi">
  <div class="heading" style="top:62px"><div class="ghost">WHAT CLIENT SAY</div><div class="title">TESTIMONIALS</div></div>
  <div class="person" style="left:58px"><div class="av" role="img" aria-label="Client portrait"></div><h4>OWEN HALE</h4><div class="role">THE CROSS FAMILY</div><p>"I couldn't be more impressed with the team at Tessa Marlow. They found my family our perfect dream home. True professionals from knowledge of the area, to the closing process and everything else in between — thank you!"</p></div>
  <div class="person" style="left:336px"><div class="av" role="img" aria-label="Client portrait"></div><h4>MARA VOSS</h4><div class="role">DEVELOPER</div><p>"I couldn't be more impressed with the team at Tessa Marlow. They found my family our perfect dream home. True professionals from knowledge of the area, to the closing process and everything else in between — thank you!"</p></div>
  <div class="person" style="left:616px"><div class="av" role="img" aria-label="Client portrait"></div><h4>REID CALLOWAY</h4><div class="role">CEO</div><p>"I couldn't be more impressed with the team at Tessa Marlow. They found my family our perfect dream home. True professionals from knowledge of the area, to the closing process and everything else in between — thank you!"</p></div>
  <div class="person" style="left:894px"><div class="av" role="img" aria-label="Client portrait"></div><h4>LENA BRISK</h4><div class="role">PROJECT MANAGER</div><p>"I couldn't be more impressed with the team at Tessa Marlow. They found my family our perfect dream home. True professionals from knowledge of the area, to the closing process and everything else in between — thank you!"</p></div>
  <div class="pager">‹ &nbsp;&nbsp; 1/4 &nbsp;&nbsp; ›</div>
</section>

<section class="blog">
  <div class="heading" style="top:56px"><div class="ghost">LASTEST NEWS FROM US</div><div class="title">OUR BLOG</div></div>
  <div class="post" style="left:63px"><div class="photo" role="img" aria-label="White farmhouse with lawn" style="background:linear-gradient(180deg,#b8c9d8,#d8d8d2 50%,#6d8a4a)"></div><div class="meta">Jan 10, 2020 &nbsp;&nbsp; By <b>Alice</b></div><h4>Unique Real Estate Marketing: Have A Tent Business Card</h4><p>Quiet acres near the ridge, with fresh water and long views over pine valley.</p><div class="more">Read More →</div></div>
  <div class="post" style="left:282px"><div class="photo" role="img" aria-label="House photo with hover overlay" style="background:#4d4f52;border:6px solid #e0e0e0"></div><div class="meta">Jan 10, 2020 &nbsp;&nbsp; By <b style="color:var(--blue)">Jason</b></div><h4>Unique Real Estate Marketing: Have A Tent Business Card</h4><p>Simple tips for buying rural land, from surveys and access roads to utilities.</p><div class="more" style="color:var(--blue)">Read More →</div></div>
  <div class="post" style="left:499px"><div class="photo" role="img" aria-label="Porch house among trees" style="background:linear-gradient(180deg,#b6c8dc,#d6c9b0 55%,#6b8a48)"></div><div class="meta">Jan 08, 2020 &nbsp;&nbsp; By <b>Jasmin</b></div><h4>Unique Real Estate Marketing: Have A Tent Business Card</h4><p>Why more families choose a quiet retreat away from busy city streets each year.</p><div class="more">Read More →</div></div>
  <div class="post" style="left:718px"><div class="photo" role="img" aria-label="Couple meeting an agent" style="background:linear-gradient(160deg,#dfe6ec,#9aa8b4)"></div><div class="meta">Dec 15, 2020 &nbsp;&nbsp; By <b>Ashley</b></div><h4>Unique Real Estate Marketing: Have A Tent Business Card</h4><p>Meet our local agents and learn how we walk every parcel before it is listed.</p><div class="more">Read More →</div></div>
  <div class="post" style="left:937px"><div class="photo" role="img" aria-label="Red house in autumn woods" style="background:linear-gradient(180deg,#8a6a4a,#6a3a2a 60%,#3d3a2a)"></div><div class="meta">Nov 26, 2020 &nbsp;&nbsp; By <b>Victoria</b></div><h4>Unique Real Estate Marketing: Have A Tent Business Card</h4><p>Planning a small cabin build on vacant land: permits, budget and timing.</p><div class="more">Read More →</div></div>
</section>

<section class="partners">
  <div class="heading" style="top:58px"><div class="ghost">FIND MORE ABOUT US</div><div class="title">OUR PARTNERS</div></div>
  <div class="partner-row">
    <span>PINECREST</span><span>STONEBROOK</span><span>MEADOWLINE HOMES</span><span><i></i>HEARTH REALTY</span><span>ALDER &amp; VALE</span>
  </div>
</section>

<section class="notify">
  <div class="abs" role="img" aria-label="Line drawing of city buildings" style="left:18px;top:18px;width:196px;height:121px;background:linear-gradient(180deg,rgba(255,255,255,.05),rgba(255,255,255,.22))"></div>
  <h3>BE NOTIFIED WHEN NEW<br>PROPERTIES BECOME<br>AVAILABLE</h3>
  <div class="input">Enter email Address</div>
  <div class="btn">NOTIFY ME</div>
  <div class="abs" role="img" aria-label="Agent holding a small house model" style="left:1010px;top:-26px;width:100px;height:165px;background:linear-gradient(180deg,#e7e7e7,#3c6ea8);border-radius:40px 40px 0 0"></div>
</section>

<section class="contact">
  <div class="abs" role="img" aria-label="Faint world map background" style="inset:0;background:radial-gradient(ellipse at center,#eef1f4,#f4f6f8)"></div>
  <div class="heading" style="top:50px"><div class="ghost">GET IN TOUCH</div><div class="title">CONTACT US</div></div>
  <div class="form-field" style="left:234px;top:135px;width:228px">FIRST NAME</div>
  <div class="form-field" style="left:471px;top:135px;width:228px">FIRST NAME</div>
  <div class="form-field" style="left:234px;top:175px;width:228px">EMAIL</div>
  <div class="form-field" style="left:471px;top:175px;width:228px">PHONE</div>
  <div class="form-field" style="left:234px;top:215px;width:465px;height:110px">MESSAGE</div>
  <div class="send">SEND</div>
  <div class="abs" role="img" aria-label="Street map with office location" style="left:712px;top:137px;width:256px;height:225px;background:linear-gradient(135deg,#eae6dc,#dcd8cc);border:1px solid #ddd"></div>
</section>

<footer class="site-footer">
  <div class="fcol" style="left:63px"><h5>CONTACT US</h5><ul>
    <li><svg width="9" height="9" viewBox="0 0 24 24"><path fill="#6f9b2c" d="M2 5h20v14H2z"/></svg>hello@quiethollowproperties.com</li>
    <li><svg width="9" height="9" viewBox="0 0 24 24"><path fill="#6f9b2c" d="M6.6 10.8a15 15 0 006.6 6.6l2.2-2.2c.3-.3.7-.4 1-.2 1.1.4 2.3.6 3.6.6.6 0 1 .4 1 1V20c0 .6-.4 1-1 1A17 17 0 013 4c0-.6.4-1 1-1h3.5c.6 0 1 .4 1 1 0 1.3.2 2.5.6 3.6.1.3 0 .7-.2 1z"/></svg>+020 5550 1234</li>
    <li><svg width="9" height="9" viewBox="0 0 24 24"><path fill="#6f9b2c" d="M12 2a7 7 0 00-7 7c0 5 7 13 7 13s7-8 7-13a7 7 0 00-7-7zm0 9a2 2 0 110-4 2 2 0 010 4z"/></svg>48 Cedar Lane, Fernbrook FB2<br><span style="margin-left:15px">4KD, United Kingdom</span></li></ul></div>
  <div class="fcol" style="left:362px"><h5>QUICK LINK</h5><ul><li>Home</li><li>About Us</li><li>Our Properties</li><li>Reviews</li><li>Our Blog</li></ul></div>
  <div class="fcol" style="left:566px"><h5>INFOMATION</h5><ul><li>My Account</li><li>Order History</li><li>Wish List</li><li>Privacy Policy</li><li>Site map</li></ul></div>
  <div class="fcol" style="left:762px"><h5>OUR POLICY</h5><ul><li>Help &amp; Contact</li><li>Return Policy</li><li>Careers</li><li>Affiliates</li><li>Legal Notice</li></ul></div>
  <div class="fcol" style="left:947px;width:190px"><h5>NEWSLETTER</h5>
    <p style="line-height:14px">To be updated on our news &amp; promotions, join our mailing list.</p>
    <div style="display:flex;margin-top:18px;height:28px"><div style="flex:1;background:#fff;color:#aaa;font-size:7px;padding:9px">Email</div><div style="width:44px;background:var(--green);color:#fff;font-size:7px;display:flex;align-items:center;justify-content:center">JOIN</div></div>
    <div style="display:flex;gap:18px;margin-top:22px"><span style="width:10px;height:10px;border-radius:50%;background:#fff"></span><span style="width:10px;height:10px;border-radius:50%;background:var(--green)"></span><span style="width:10px;height:10px;border-radius:50%;background:#fff"></span><span style="width:10px;height:10px;border-radius:50%;background:#fff"></span></div>
  </div>
  <div class="copy">Copyright © 2020 <b>quiethollowproperties.com</b>. All right reserved.</div>
</footer>

</body>
</html>
```